Need a clean & modern homepage for an education site + opportunity for longer term work

Thanks for viewing our project. We are excited about this new website and we hope that we might build a relationship with designers as we work on this project. I provided quite a few details and requirements to help you more quickly create a design that meets our needs.
Who we are:
We are a website that discusses the importance of college accreditation and provides a directory of college programs.
What we need:
A homepage that meets the below requirements and is inspired by the examples provided
Definition of accredited:
ac·cred·it·ed [uh-kred-i-tid] adj.
1. officially recognized as meeting the essential requirements, as of academic excellence: accredited schools.
2. provided with official credentials, as by a government: an accredited diplomatic representative.
3. accepted as authoritative: an accredited theory.
Overall look and feel for the homepage:
- Clean, simple and modern
- Limited (or zero) pictures
- Utilize color blocks with text
- A trend seems to be longer vertical length homepages with lots of whitespace. I generally like this trend as long as the page is not way to tall.
Inspirations: Sites that have a similar look and feel to what I need.
http://lernvoxa.org/
http://www.campusmetrik.com/colleges/brantmoor-university/
http://quietfolding.org/
http://www.velostrahiring.com/
http://www.zunq.com/
http://sketches.bxv.com/
Items to be included on the homepage. Details below on each item.
- Top navigation
- Logo: Please leave a blank area for a logo. The logo has not been designed.
- Simple graphic/color block at the top that highlights a definition of “Accredited” – the definition should be formatted like it is being copy/pasted from a dictionary.
- Space for a video and small (50 word) written description of the video. You can use placeholder text.
- One section with 3 Paragraphs of content (each paragraph around 100 words) with a header at the top. You can use placeholder text but please create the formatting. At the end of the 3 paragraphs please have a “Read More” Note this shouldn't be 3 separate paragraphs with three read mores - it is 3 paragraphs with one read more at the end.
- An area with the header “Search Colleges by State” that has anchor text links to all 50 states.
Top navigation:
- Home
- States – with a subnav dropdown that includes all 50 US states.
- Programs – with a subnav dropdown that includes program titles (list below)
- Degrees - with a subnav dropdown that includes 5 degree levels (list below)
- Accreditation – no subnav
- Rankings – no subnav
- Resources – no subnav
Footer
- Link to about us, privacy, and a copyright www.url.com
Programs List for sub navigation
Accounting
Art
Bible
Business
Criminal Justice
Design
Education
Engineering
English
Law
LPN to RN
Management
Math
MBA
MPH
Medical Assisting
Military
Nursing
Occupational Therapy
Paralegal
Psychology
Pharmacy
RN to BSN
Radiology
Social Work
Sonography
Degrees list for sub navigation
Certificate
Associate
Bachelors
Masters
PhD
Thanks so much - looking forward to working with you!
Education

```html
<!DOCTYPE html>
<html lang="en">
<head>
<meta charset="utf-8">
<title>Accredited – Homepage</title>
<link href="https://fonts.googleapis.com/css2?family=Lato:ital,wght@0,400;0,700;1,400&family=Tinos:wght@400;700&display=swap" rel="stylesheet">
<style>
:root{
  --white:#ffffff;
  --ink:#1b1b1b;
  --nav-active:#15a2e6;
  --hero:#0b87d6;
  --charcoal:#2b3239;
  --teal:#24b897;
  --cyan:#22aec8;
  --violet:#8c88bf;
  --sky-text:#1b9ce0;
  --body-text:#3a3a3a;
  --navy:#0b67a3;
  --coral:#f2685f;
  --bright:#06a8ec;
  --footer:#343b45;
  --footer-text:#e6e8ea;
}
*{margin:0;padding:0;box-sizing:border-box}
html,body{width:1200px;height:2544px;overflow:hidden}
body{position:relative;font-family:"Lato",Arial,sans-serif;background:var(--white);color:var(--ink)}
a{color:inherit;text-decoration:none}

/* header */
.site-header{position:absolute;left:0;top:0;width:1200px;height:138px;background:var(--white)}
.social{position:absolute;left:913px;top:16px;display:flex;gap:4px}
.social span{width:22px;height:22px;display:block}
.social .s1{background:#3b5b9a}.social .s2{background:#33a9e0}.social .s3{background:#d34836}.social .s4{background:#c7222a}
.brand{position:absolute;left:198px;top:70px;font-size:38px;font-weight:700;letter-spacing:1px}
.main-nav{position:absolute;left:376px;top:82px;display:flex;align-items:center;font-size:15px;height:28px}
.main-nav a{position:absolute;white-space:nowrap;line-height:28px}
.main-nav .is-active{background:var(--nav-active);color:var(--white);padding:0 8px;line-height:26px}
.main-nav .accent{color:var(--nav-active)}
.caret{display:inline-block;width:6px;height:6px;border-right:1px solid #999;border-bottom:1px solid #999;transform:rotate(45deg);margin-left:5px;position:relative;top:-3px}

/* hero definition */
.hero{position:absolute;left:0;top:138px;width:1200px;height:320px;background:var(--hero);color:var(--white);font-family:"Tinos","Times New Roman",serif}
.word{position:absolute;left:200px;top:88px;font-size:58px;font-weight:700;letter-spacing:1px}
.pron{position:absolute;left:200px;top:155px;font-size:44px}
.pron i{font-style:italic}
.senses{position:absolute;left:636px;top:104px;font-size:17px;line-height:20px;list-style:none;width:420px}
.senses li{padding-left:18px;text-indent:-18px}
.hero-arrow{position:absolute;left:485px;top:205px}

/* feature cards */
.features{position:absolute;left:0;top:466px;width:1200px;height:416px;background:var(--charcoal)}
.card{position:absolute;top:56px;width:286px;height:302px;color:var(--white);text-align:center}
.card.ranking{left:150px;background:var(--teal)}
.card.accreditation{left:456px;background:var(--cyan)}
.card.resources{left:762px;background:var(--violet)}
.card-icon{position:absolute;left:111px;top:24px}
.card h2{position:absolute;left:0;width:100%;top:96px;font-size:30px;font-weight:700}
.card p{position:absolute;left:26px;width:234px;top:148px;font-size:12.5px;line-height:17px}

/* video */
.video-section{position:absolute;left:0;top:882px;width:1200px;height:564px;background:var(--white)}
.video-section h2{position:absolute;left:0;width:100%;top:52px;text-align:center;color:var(--sky-text);font-size:40px;font-weight:700}
.video-section p{position:absolute;left:145px;width:910px;top:126px;text-align:center;color:var(--body-text);font-size:17px;line-height:23px}
.laptop{position:absolute;left:272px;top:268px}

/* article */
.article{position:absolute;left:0;top:1446px;width:1200px;height:538px;background:var(--navy);color:var(--white)}
.article h2{position:absolute;left:148px;top:46px;font-size:36px;font-weight:700}
.article .copy{position:absolute;left:148px;top:112px;width:520px;font-size:12px;line-height:17px;color:#d8e6f1}
.article .copy p{margin-bottom:17px}
.read-more{position:absolute;left:150px;top:442px;width:120px;height:40px;background:var(--coral);color:var(--white);font-size:14px;line-height:40px;text-align:center;text-transform:uppercase}
.chart{position:absolute;left:686px;top:122px}

/* states */
.states{position:absolute;left:0;top:1990px;width:1200px;height:356px;background:var(--bright)}
.states-title{position:absolute;left:304px;top:38px;width:592px;height:72px;background:var(--white);outline:2px solid var(--white);outline-offset:4px;border:2px solid var(--bright);color:var(--sky-text);font-size:34px;font-weight:700;text-align:center;line-height:66px}
.state-col{position:absolute;top:146px;list-style:none}
.state-col li{font-size:15px;font-style:italic;line-height:34px;color:var(--white);text-decoration:underline}

/* footer */
.site-footer{position:absolute;left:0;top:2348px;width:1200px;height:196px;background:var(--footer);color:var(--footer-text);text-align:center}
.footer-brand{position:absolute;left:0;width:100%;top:44px;font-size:38px;font-weight:700;color:var(--white)}
.footer-links{position:absolute;left:0;width:100%;top:100px;font-size:15px}
.footer-links span{margin:0 10px}
.footer-url{position:absolute;left:0;width:100%;top:142px;font-size:14px;font-style:italic}
</style>
</head>
<body>

<header class="site-header">
  <div class="social"><span class="s1"></span><span class="s2"></span><span class="s3"></span><span class="s4"></span></div>
  <div class="brand">LOGO</div>
  <nav class="main-nav">
    <a class="is-active" style="left:0">Home</a>
    <a style="left:76px">States<span class="caret"></span></a>
    <a style="left:152px">Programs<span class="caret"></span></a>
    <a class="accent" style="left:256px">Degrees<span class="caret"></span></a>
    <a style="left:348px">Accreditation</a>
    <a style="left:473px">Rankings</a>
    <a style="left:574px">Resources</a>
  </nav>
</header>

<section class="hero">
  <div class="word">ac·cred·it·ed</div>
  <div class="pron">[uh-kred-i-tid] <i>adj.</i></div>
  <ol class="senses">
    <li>1. officially recognized as meeting the essential requirements, as of academic excellence: accredited schools.</li>
    <li>2. provided with official credentials, as by a government: an accredited diplomatic representative.</li>
    <li>3. accepted as authoritative: an accredited theory.</li>
  </ol>
  <svg class="hero-arrow" width="190" height="50" viewBox="0 0 190 50">
    <path d="M4 32 Q90 58 180 14" fill="none" stroke="#fff" stroke-width="2.5" stroke-linecap="round"/>
    <path d="M166 10 L182 13 L176 28" fill="none" stroke="#fff" stroke-width="2.5" stroke-linecap="round" stroke-linejoin="round"/>
  </svg>
</section>

<section class="features">
  <article class="card ranking">
    <svg class="card-icon" width="64" height="64" viewBox="0 0 64 64"><circle cx="32" cy="32" r="32" fill="#e8f0ee"/><path d="M22 18h20v8a10 10 0 0 1-20 0z" fill="#7a8c88"/><rect x="29" y="36" width="6" height="7" fill="#7a8c88"/><rect x="24" y="43" width="16" height="4" fill="#7a8c88"/></svg>
    <h2>Ranking</h2>
    <p>Lorem ipsum dolor sit amet, consectetur adipiscing elit. Fusce rutrum magna in nisi mattis, ut mollis lorem dictum. Morbi ac condimentum lacus. Phasellus dolor magna, rhoncus et interdum eget, tempor non sapien.</p>
  </article>
  <article class="card accreditation">
    <svg class="card-icon" width="64" height="64" viewBox="0 0 64 64"><circle cx="32" cy="32" r="32" fill="#e8f0ee"/><circle cx="32" cy="30" r="12" fill="none" stroke="#7a8c88" stroke-width="4"/><path d="M25 40l-4 12 6-3 3 5 2-12zM39 40l4 12-6-3-3 5-2-12z" fill="#7a8c88"/></svg>
    <h2>Accreditation</h2>
    <p>Lorem ipsum dolor sit amet, consectetur adipiscing elit. Fusce rutrum magna in nisi mattis, ut mollis lorem dictum. Morbi ac condimentum lacus. Phasellus dolor magna, rhoncus et interdum eget, tempor non sapien.</p>
  </article>
  <article class="card resources">
    <svg class="card-icon" width="64" height="64" viewBox="0 0 64 64"><circle cx="32" cy="32" r="32" fill="#e8f0ee"/><path d="M12 28l20-9 20 9-20 9z" fill="#7a8c88"/><path d="M20 32v8c4 4 20 4 24 0v-8l-12 6z" fill="#7a8c88"/></svg>
    <h2>Resources</h2>
    <p>Lorem ipsum dolor sit amet, consectetur adipiscing elit. Fusce rutrum magna in nisi mattis, ut mollis lorem dictum. Morbi ac condimentum lacus. Phasellus dolor magna, rhoncus et interdum eget, tempor non sapien.</p>
  </article>
</section>

<section class="video-section">
  <h2>WATCH OUR VIDEO</h2>
  <p>Lorem ipsum dolor sit amet, consectetur adipiscing elit. Fusce rutrum magna in nisi mattis, ut mollis lorem dictum. Morbi ac condimentum lacus. Phasellus dolor magna, rhoncus et interdum eget, tempor non sapien. Nullam fermentum ultrices ipsum non molestie. Nunc vitae nulla ut felis ultrices mollis nec vel felis. Sed vehicula orci a orci vehicula mattis. Cum sociis natoque penatibus et magnis dis parturient montes, nascetur ridiculus mus.</p>
  <svg class="laptop" width="656" height="180" viewBox="0 0 656 180" overflow="visible">
    <defs>
      <linearGradient id="still" x1="0" y1="0" x2="1" y2="1">
        <stop offset="0" stop-color="#c9b9a0"/><stop offset="0.5" stop-color="#8a6e55"/><stop offset="1" stop-color="#3e3229"/>
      </linearGradient>
    </defs>
    <rect x="72" y="0" width="492" height="282" rx="10" fill="#2a2d31"/>
    <rect x="92" y="18" width="452" height="224" fill="url(#still)" role="img" aria-label="Video still of a presenter speaking"/>
    <circle cx="318" cy="128" r="34" fill="none" stroke="#fff" stroke-width="4" opacity="0.9"/>
    <path d="M308 110 L334 128 L308 146 Z" fill="#fff" opacity="0.9"/>
    <rect x="92" y="242" width="452" height="24" fill="#dfe3e7"/>
    <path d="M100 248 L110 254 L100 260 Z" fill="#333"/>
    <rect x="150" y="251" width="232" height="6" rx="3" fill="#b9c1c8"/>
    <rect x="150" y="251" width="180" height="6" rx="3" fill="#3d8ed6"/>
    <rect x="414" y="249" width="40" height="10" fill="#9aa2aa"/>
    <rect x="0" y="282" width="656" height="14" rx="4" fill="#b3b7bb"/>
  </svg>
</section>

<section class="article">
  <h2>Header Title 1</h2>
  <div class="copy">
    <p>Lorem ipsum dolor sit amet, consectetur adipiscing elit. Fusce rutrum magna in nisi mattis, ut mollis lorem dictum. Morbi ac condimentum lacus. Phasellus dolor magna, rhoncus et interdum eget, tempor non sapien.</p>
    <p>Nunc vitae nulla ut felis ultrices mollis nec vel felis. Sed vehicula orci a orci vehicula mattis. Cum sociis natoque penatibus et magnis dis parturient montes, nascetur ridiculus mus. Nulla ullamcorper risus eu justo pellentesque consequat.</p>
    <p>Phasellus a convallis dui, id laoreet turpis. Cras condimentum odio sed gravida accumsan. Proin posuere vitae erat id convallis. Cras tempus, elit eget condimentum pretium, lacus nisl rhoncus neque, ac semper justo purus vel lacus. Mauris scelerisque lobortis quam sit amet tristique. Sed ullamcorper molestie hendrerit. Fusce varius eget felis eget tincidunt. Nulla a vehicula nisi, vel aliquam diam. Nulla tincidunt tortor nisl, malesuada placerat elit facilisis dictum. Etiam sit amet felis euismod odio dignissim aliquet. Duis ac fringilla sem, euismod pretium nunc. Vestibulum vel mattis nisl. Nullam imperdiet eros vel metus vestibulum, at ornare elit consectetur.</p>
  </div>
  <a class="read-more">Readmore</a>
  <svg class="chart" width="360" height="200" viewBox="0 0 360 200" font-family="Lato, sans-serif" font-size="10" font-weight="700" fill="#fff" text-anchor="middle">
    <path d="M4 194 L356 194 L344 178 L16 178 Z" fill="#e9efe0"/>
    <g>
      <rect x="30" y="20" width="22" height="158" fill="#e8403a"/><text x="41" y="14">100%</text>
      <rect x="66" y="52" width="22" height="126" fill="#2fa9dc"/><text x="77" y="46">80%</text>
      <rect x="102" y="68" width="22" height="110" fill="#f2a61f"/><text x="113" y="62">70%</text>
      <rect x="138" y="99" width="22" height="79" fill="#8db339"/><text x="149" y="93">50%</text>
      <rect x="174" y="36" width="22" height="142" fill="#e8403a"/><text x="185" y="30">90%</text>
      <rect x="210" y="83" width="22" height="95" fill="#2fa9dc"/><text x="221" y="77">60%</text>
      <rect x="246" y="60" width="22" height="118" fill="#f2a61f"/><text x="257" y="54">75%</text>
      <rect x="282" y="28" width="22" height="150" fill="#8db339"/><text x="293" y="22">95%</text>
    </g>
  </svg>
</section>

<section class="states">
  <h2 class="states-title">Search Colleges by State</h2>
  <ul class="state-col" style="left:168px"><li>California</li><li>Texas</li><li>Illinois</li><li>Virginia</li><li>Massachusetts</li></ul>
  <ul class="state-col" style="left:322px"><li>Kentucky</li><li>Florida</li><li>New Jersy</li><li>Pennsylvania</li><li>Alaska</li></ul>
  <ul class="state-col" style="left:479px"><li>Louisiana</li><li>Arizona</li><li>Georgia</li><li>Tennessee</li><li>Colorado</li></ul>
  <ul class="state-col" style="left:626px"><li>California</li><li>Texas</li><li>Illinois</li><li>Virginia</li><li>Massachusetts</li></ul>
  <ul class="state-col" style="left:780px"><li>Kentucky</li><li>Florida</li><li>New Jersy</li><li>Pennsylvania</li><li>Alaska</li></ul>
  <ul class="state-col" style="left:937px"><li>Louisiana</li><li>Arizona</li><li>Georgia</li><li>Tennessee</li><li>Colorado</li></ul>
</section>

<footer class="site-footer">
  <div class="footer-brand">LOGO</div>
  <div class="footer-links">about us <span>|</span> privacy <span>|</span> copyright</div>
  <div class="footer-url">www.url.com</div>
</footer>

</body>
</html>
```